Internet Of Things brochure

Need to create a brochure with a common theme to our website and the last 2 pages of the attached file. All the contect is in the file that I have attached.
website www.pendomar.com.au

```html
<!DOCTYPE html>
<html lang="en">
<head>
<meta charset="utf-8">
<title>Digital Solutions Brochure Spread</title>
<link rel="stylesheet" href="https://fonts.googleapis.com/css2?family=Exo+2:ital,wght@0,400;0,500;0,600;1,400&family=Titillium+Web:ital,wght@0,300;0,400;0,600;1,300;1,400&display=swap">
<style>
:root{
  --ink:#2a2a30;
  --ink-soft:#45454d;
  --paper:#ffffff;
  --band:#e8e8ea;
  --navy-top:#1b1450;
  --navy-mid:#1a1f5e;
  --navy-bottom:#0f2b6c;
  --violet-box-a:#2d2372;
  --violet-box-b:#1c3a8c;
  --on-dark:#e9ecf8;
  --on-dark-soft:#c9cfe8;
  --stage:#f2f3f5;
}
*{margin:0;padding:0;box-sizing:border-box}
html,body{width:1200px;height:933px;overflow:hidden;background:var(--stage)}
.spread{position:relative;width:1200px;height:933px;display:flex}
.page{position:relative;width:600px;height:933px;overflow:hidden}
.page--light{background:var(--paper);color:var(--ink);font-family:"Titillium Web",sans-serif}
.page--dark{background:linear-gradient(180deg,var(--navy-top) 0%,var(--navy-mid) 50%,var(--navy-bottom) 100%);color:var(--on-dark);font-family:"Titillium Web",sans-serif}
.section{position:absolute;left:0;width:600px}
.heading{font-family:"Exo 2",sans-serif;font-weight:500;font-size:16px;letter-spacing:.2px;line-height:1.15;text-transform:uppercase}
.subheading{font-style:italic;font-size:10.5px;line-height:1.2;color:var(--ink-soft)}
.body{font-size:10.5px;line-height:1.32;text-align:justify;font-weight:400}
.body + .body{margin-top:11px}
.intro{top:0;height:196px;padding:42px 40px 0}
.intro .subheading{margin-bottom:14px}
.feature-band{top:196px;height:243px;background:var(--band);display:flex}
.feature-band__text{width:226px;padding:9px 12px 0 40px}
.feature-band__text .body{font-size:10.5px;line-height:1.28}
.feature-band__photo{flex:1;background:linear-gradient(120deg,#6b7078 0%,#9aa0a6 40%,#c8a93a 75%,#e5c43a 100%)}
.disruption{top:439px;height:174px;padding:24px 40px 0}
.disruption .heading{margin-bottom:3px}
.question-band{top:613px;height:205px;display:flex}
.question-band__photo{width:300px;background:linear-gradient(135deg,#d7d9dc 0%,#b5b9bd 45%,#3c3f44 100%)}
.question-band__box{flex:1;background:linear-gradient(180deg,var(--violet-box-a),var(--violet-box-b));color:var(--on-dark);padding:20px 26px 0 20px}
.question-band__lead{font-size:11px;font-weight:600;margin-bottom:2px}
.question{font-style:italic;font-size:10.5px;line-height:1.3;font-weight:300;color:var(--on-dark-soft);margin-bottom:13px}
.closing{top:818px;height:115px;padding:14px 40px 0}
.solutions{top:0;height:488px;padding:42px 30px 0 34px}
.page--dark .heading{color:#fff}
.solutions__intro{font-size:10.5px;line-height:1.3;color:var(--on-dark-soft);margin-top:2px}
.scenarios__lead{font-size:11.5px;font-weight:600;margin-top:10px;color:#fff}
.scenario{font-size:10.3px;line-height:1.3;font-style:italic;font-weight:300;color:var(--on-dark-soft);margin-bottom:8px}
.scenario b{font-style:normal;font-weight:600;color:#fff;margin-right:3px}
.helping__title{font-family:"Exo 2",sans-serif;font-weight:500;font-size:15.5px;color:#fff;text-align:center;margin:10px 0 10px}
.offer-grid{display:grid;grid-template-columns:250px 220px;column-gap:30px;row-gap:8px;padding-left:42px}
.offer__title{font-family:"Exo 2",sans-serif;font-size:12px;font-weight:500;line-height:1.25;color:#fff;margin-bottom:1px}
.offer__list{list-style:none}
.offer__list li{font-size:11px;line-height:1.3;color:var(--on-dark-soft)}
.offer__list li::before{content:"· "}
.dashboard-photo{top:488px;height:225px;background:linear-gradient(100deg,#2b2f36 0%,#4a4f57 35%,#3a3e45 55%,#5a2f36 80%,#262a31 100%)}
.workshop{top:713px;height:220px;padding:16px 34px 0 34px}
.workshop .body{color:var(--on-dark-soft);font-size:10.3px;line-height:1.3}
.workshop .body + .body{margin-top:12px}
.workshop__cta{font-style:italic;font-size:10.5px;color:var(--on-dark-soft);margin-top:14px}
</style>
</head>
<body>
<main class="spread">
  <section class="page page--light">
    <div class="section intro">
      <h2 class="heading">Embrace digital or risk being left behind</h2>
      <p class="subheading">Does your business have the Digital DNA required to succeed in the digital era?</p>
      <p class="body">Embracing the new revolution in digital technology is more than just having an eCommerce website - its about what is possible when every aspect of your business harnesses the power of digital innovation. When the sum of your business parts utilise digital and link together then your business can completely transform through being more effective, productive and automated.</p>
      <p class="body">The way businesses operate has forever been changed by advancements in digital technology. Integrated systems allow for sophisticated e-Commerce, automated business operations, digital marketing, CRMs and learning &amp; development opportunities.</p>
    </div>
    <div class="section feature-band">
      <div class="feature-band__text">
        <p class="body">These can be connected together so that digital-ready businesses have never been more agile, nimble and ready to compete and serve. These elements combined amount to a serious threat to those who utilise a traditional business model and don't or can't adapt.</p>
        <p class="body">Many enterprises have failed to adapt to this change. Through not integrating their business into the digital ecosystem, it exposes them to the possibility of failing to properly engage with their customers.</p>
      </div>
      <div class="feature-band__photo" role="img" aria-label="Photo of an engineer using a tablet beside a yellow industrial robot arm in a factory"></div>
    </div>
    <div class="section disruption">
      <h2 class="heading">The age of digital disruption is here</h2>
      <p class="body">The world's largest taxi firm, Ridora, owns no vehicles. The world's largest accommodation provider, Staylo, owns no real estate. The world's biggest phone companies, Callvane and Chatmoor, own no telco infrastructure. The world's most valuable retailer, Marketon, carries no stock. The most popular media company, Friendwall, creates no content. The world's largest movie house, Reelhaus, owns no cinemas. Something big has happened. It's called digital disruption.</p>
      <p class="body">Creating and controlling the marketplace between the consumer and DIGITAL the provider of the goods or services is now the most valuable place to be. This is where risk is low, costs are slashed and profits are maximized. This digital revolution poses both a significant threat and a significant opportunity.</p>
    </div>
    <div class="section question-band">
      <div class="question-band__photo" role="img" aria-label="Photo of a tablet showing a fleet management dashboard with a map and coloured tiles"></div>
      <div class="question-band__box">
        <p class="question-band__lead">So ask yourself:</p>
        <p class="question">Is your business capable of responding quickly to digital threats?</p>
        <p class="question">Are you doing all you can to compete in the digital business environment?</p>
        <p class="question">Are you considering alternative business models and opportunities available through digitization?</p>
        <p class="question">Does your business continue to grow in value in the face of digital threats?</p>
      </div>
    </div>
    <div class="section closing">
      <p class="body">Pendomar Digital works closely with you to identify and focus on the valuable digital opportunities available to your business operation, re-design your processes and prepare your business for the task of competing in the global digital environment. Partner with us and you'll discover what is possible for your business - and how you can take your business to another level.</p>
    </div>
  </section>

  <section class="page page--dark">
    <div class="section solutions">
      <h2 class="heading">Digital solutions</h2>
      <p class="solutions__intro">Our digital solutions are varied - impacting all parts of the business model and are completely tailored to your business and your industry.</p>
      <p class="scenarios__lead">We can cover the following scenarios (and more):</p>
      <p class="scenario"><b>a)</b>Introduce a digitally strategic business model, digitising operations and processes by leveraging cloud-based applications and mobile devices that digitise data collection and collation and supply chain processes.</p>
      <p class="scenario"><b>b)</b>Learning &amp; Development solutions that comprise an array of digitised approaches that are always available on the Cloud, can be built in minutes, are completely customisable, are easy to maintain and are mobile friendly.</p>
      <p class="scenario"><b>c)</b>Seamlessly integrating digital commerce into your existing brick &amp; mortar business quickly, strategically and cost effectively - helping you compete.</p>
      <p class="scenario"><b>d)</b>Creating targeted and measurable digital marketing campaigns that focus on increasing first-time and repeat sales and building long-term customer loyalty.</p>
      <h3 class="helping__title">How we're helping businesses reimagine their business through digital</h3>
      <div class="offer-grid">
        <div class="offer">
          <h4 class="offer__title">Digital Commerce</h4>
          <ul class="offer__list"><li>eCommerce</li><li>mCommerce</li><li>Digital payment integration</li><li>Logistics and Supply Chain Integration</li></ul>
        </div>
        <div class="offer">
          <h4 class="offer__title">Digital Business Solutions</h4>
          <ul class="offer__list"><li>Cloud ERP, CRM, SCM, HCM</li><li>IOT Integration to ERP, CRM, SCM</li><li>Digital invoicing solutions</li><li>Any device ERP, CRM, SCM</li></ul>
        </div>
        <div class="offer">
          <h4 class="offer__title">Digital Marketing</h4>
          <ul class="offer__list"><li>SEO &amp; SEM</li><li>Marketing Insights &amp; Analytics</li><li>Responsive EDMs and Digital Campaigns</li><li>Digital CTA</li><li>Proximity Marketing</li></ul>
        </div>
        <div class="offer">
          <h4 class="offer__title">Digital Learning</h4>
          <ul class="offer__list"><li>Cloud LMS</li><li>Learning &amp; Development Solutions</li><li>Campus On Cloud</li></ul>
        </div>
      </div>
    </div>
    <div class="section dashboard-photo" role="img" aria-label="Photo of hands holding a tablet with a map-based automation dashboard in front of city towers"></div>
    <div class="section workshop">
      <h2 class="heading">Discovery workshop</h2>
      <p class="body">The Digital Discovery Workshop is a half-day opportunity for the Key Stakeholders of your business that allows Pendomar Digital to identify and explore which areas of your business are best suited to a digital transformation. During this workshop you will also learn about the threats that the digital environment may pose to your business specifically, and the opportunities and possibilities that exist by applying digital solutions to your existing business.</p>
      <p class="body">We also provide our clients with the opportunity to consider the overall strategy and actions needed within their organization to help them develop a competitive advantage inside the context of the ever-changing digital business environment. This analysis is relevant to all business types and industries.</p>
      <p class="workshop__cta">Interested in discovering your digital opportunities?</p>
    </div>
  </section>
</main>
</body>
</html>
```